VELORA Brisbane Tiling Service

My name is Milos Brendt i need a business card for a new company. We are wall and floor tilers based in Brisbane, our company is Velorix Brisbane Tiling Service.
We would like a logo from our website used on our cards. Our website is www.velorix.com.au

I would like my Chatterbook and Postwave accounts on my card.

Industry/Entity Type

Business

Colors
0692cd
3176b5
33a6d7
85cae6

```html
<!DOCTYPE html>
<html lang="en">
<head>
<meta charset="utf-8">
<title>Velorix Brisbane Tiling Service – Business Card</title>
<link rel="stylesheet" href="https://fonts.googleapis.com/css2?family=Tinos&family=Arimo&family=Montserrat:wght@400;600;700&display=swap">
<style>
  :root {
    --backdrop: #e9e7e4;
    --card: #ffffff;
    --brand-blue: #3176b5;
    --brand-deep: #1f64a8;
    --brand-light: #33a6d7;
    --ink: #111111;
    --rule: #d6dde6;
  }
  * { margin: 0; padding: 0; box-sizing: border-box; }
  html, body {
    width: 1200px; height: 1000px; overflow: hidden;
    background: var(--backdrop);
  }
  .canvas { position: relative; width: 1200px; height: 1000px; }
  .card {
    position: absolute; left: 265px; width: 665px; height: 397px;
    background: var(--card);
    box-shadow: 0 6px 14px rgba(0,0,0,.18);
  }
  .card--front { top: 73px; }
  .card--back { top: 532px; }

  .brand { position: absolute; text-align: center; }
  .brand__mark {
    display: block; margin: 0 auto;
    background: linear-gradient(135deg, var(--brand-light), var(--brand-deep));
  }
  .brand__name {
    font-family: "Tinos", "Times New Roman", serif;
    color: var(--ink); line-height: 1; letter-spacing: 1px;
  }
  .brand__tagline {
    font-family: "Arimo", Arial, sans-serif;
    color: var(--brand-blue); line-height: 1;
  }

  .card--front .brand { left: 30px; top: 80px; width: 272px; }
  .card--front .brand__mark { width: 143px; height: 146px; }
  .card--front .brand__name { font-size: 46px; margin-top: 16px; }
  .card--front .brand__tagline { font-size: 22.5px; margin-top: 6px; }

  .card--back .brand { left: 0; top: 48px; width: 665px; }
  .card--back .brand__mark { width: 183px; height: 187px; }
  .card--back .brand__name { font-size: 60px; margin-top: 20px; }
  .card--back .brand__tagline { font-size: 29px; margin-top: 8px; }

  .divider {
    position: absolute; left: 322px; top: 66px; width: 1px; height: 266px;
    background: var(--rule);
  }
  .contact {
    position: absolute; left: 338px; top: 75px;
    font-family: "Montserrat", Arial, sans-serif;
    color: var(--ink); font-size: 15.5px; line-height: 23px;
  }
  .contact__name { color: var(--brand-blue); font-weight: 700; font-size: 19px; line-height: 22px; }
  .contact__role { font-size: 16px; line-height: 20px; }
  .contact__group { margin-top: 13px; }
  .contact__group--social { margin-top: 16px; line-height: 27px; }
  .label { color: var(--brand-blue); font-weight: 600; }
  .social__square {
    display: inline-block; width: 15px; height: 15px; margin-right: 6px;
    background: var(--brand-blue); vertical-align: -2px;
  }
</style>
</head>
<body>
<main class="canvas">
  <section class="card card--front" aria-label="Business card front">
    <div class="brand">
      <span class="brand__mark" role="img" aria-label="Velora brand square"></span>
      <div class="brand__name">VELORA</div>
      <div class="brand__tagline">Brisbane Tiling Service</div>
    </div>
    <div class="divider"></div>
    <div class="contact">
      <div class="contact__name">Milos Brendt</div>
      <div class="contact__role">Founder</div>
      <div class="contact__group">
        <div><span class="label">Abn:</span> 51824073619</div>
        <div><span class="label">Qbcc:</span> 1094532</div>
      </div>
      <div class="contact__group">
        <div><span class="label">Tel:</span> 0400 555 019</div>
        <div><span class="label">Tel:</span> 07 3000 0142</div>
        <div><span class="label">Email:</span> info@velorix.com.au</div>
      </div>
      <div class="contact__group contact__group--social">
        <div><span class="social__square"></span><span class="label">Postwave</span> @Infovelorix</div>
        <div><span class="social__square"></span><span class="label">Chatterbook</span> Velorix - Brisbane Tiling Service</div>
      </div>
    </div>
  </section>

  <section class="card card--back" aria-label="Business card back">
    <div class="brand">
      <span class="brand__mark" role="img" aria-label="Velora brand square"></span>
      <div class="brand__name">VELORA</div>
      <div class="brand__tagline">Brisbane Tiling Service</div>
    </div>
  </section>
</main>
</body>
</html>
```